Government Contracting business needs a website design.

Pellworth & Quine, LLC is a minority owned Service Disabled Veteran Owned Small Business (SDVOSB) that provides Strategic Planning, Public Health Emergency Response, and Data Management Solutions for Federal Civilian and Defense Agencies. We have over 20 years of experience helping health and defense agencies develop concept of operations, deploy assets and personnel in Hot Zones around the world, and deliver goods and services all of the globe.

We are a leader in the field of Data Management. We help our customers develop cloud migration and disaster recovery strategies. We are experts with database management, data replication, queries, consolidation, and records management.

We are looking for a very nice and simple website designs that states clearly what we do as a company and that is easy for our customers to follow. We would like to have some moving pictures that are base on our expertise. We want the website to be easy to use and have the scroll down features that keeps things all on the same page when clicking on the menu. I attached a document with what we need on the website. I will also attach our logo. We want it to look simple clean and very professional.

Target Market(s)

Government Contracting, Management Consulting, Health

Industry/Entity Type

Government

Coding

Coded - Design and coding required

Number of Pages Required

1 page

Font styles to use
Serif

Requirements
Must have
• Very nice picture slides that speaks to our capabilities in Disaster Response, Strategic Planning, and Database Management. Slick look and design. Make sure SDVOSB Logo is right at the beginning of website as our customers is looking for that certification. Very nice colors that blend well with our logo.
Nice to have
• Very nice and slick colors that blends well with logo.
Should not have
• Basic website design that are weary on the eye. No bright colors, just simple colors that looks good with logo.

```html
<!DOCTYPE html>
<html lang="en">
<head>
<meta charset="utf-8">
<title>Pellworth &amp; Quine, LLC</title>
<link rel="stylesheet" href="https://fonts.googleapis.com/css2?family=Libre+Baskerville:wght@400;700&family=Lora:wght@400;600&family=Open+Sans:wght@400;600&display=swap">
<style>
:root{
  --navy:#0f2a44;
  --navy-deep:#0a1f34;
  --blue:#1d4f7c;
  --accent:#2f6ea3;
  --ink:#2b3440;
  --muted:#6d7682;
  --rule:#d5dbe2;
  --soft:#eef1f4;
  --white:#ffffff;
}
*{box-sizing:border-box;margin:0;padding:0}
html,body{width:1200px;height:2300px;overflow:hidden}
body{background:var(--white);font-family:"Open Sans",sans-serif;color:var(--ink);position:relative}
.serif{font-family:"Libre Baskerville",serif}

/* hero */
.hero{position:relative;height:620px;overflow:hidden}
.hero-visual{position:absolute;inset:0;background:
  radial-gradient(ellipse at 72% 48%,#3a8fd0 0%,#1a5a92 28%,#0d3358 60%,#081d33 100%)}
.site-nav{position:absolute;top:0;left:0;right:0;height:78px;background:rgba(6,22,40,.55);display:flex;align-items:center;padding:0 80px}
.brand{display:flex;align-items:center;gap:12px;color:var(--white);font-family:"Libre Baskerville",serif;font-size:22px}
.brand-square{width:30px;height:30px;border:2px solid var(--white)}
.nav-links{margin-left:auto;display:flex;gap:44px;font-size:13px;letter-spacing:1px;color:#dbe6f0}
.nav-badge{margin-left:40px;width:60px;height:60px;border-radius:50%;background:#e8ecf0;border:3px solid #9fb1c3}
.hero-copy{position:absolute;left:80px;top:258px;width:470px;color:var(--white)}
.hero-copy h1{font-family:"Libre Baskerville",serif;font-weight:400;font-size:50px;margin-bottom:30px}
.hero-copy p{font-size:13px;line-height:1.8;color:#d6e2ee}
.slider-dots{position:absolute;left:80px;top:572px;display:flex;gap:10px}
.slider-dots span{width:14px;height:14px;border-radius:50%;border:2px solid var(--white)}
.slider-dots span.active{background:var(--white)}

/* services */
.services{display:flex;gap:40px;padding:40px 80px 0;height:430px}
.service{flex:1}
.service-visual{height:210px}
.v-disaster{background:linear-gradient(135deg,#8a3a2a,#c9a23c 55,#5a2a22)}
.v-disaster{background:linear-gradient(135deg,#7d3326,#c59b3a 55%,#4a2a26)}
.v-strategy{background:linear-gradient(135deg,#c9c2b6,#e9e4dc 55%,#8f8577)}
.v-data{background:linear-gradient(135deg,#3d4b5a,#7a8ea3 55%,#2a3440)}
.service h2{font-family:"Libre Baskerville",serif;font-weight:400;color:var(--blue);font-size:21px;margin:32px 0 14px}
.service p{font-size:13px;line-height:1.75;color:var(--muted)}

/* why hire us */
.why{background:var(--soft);height:430px;margin-top:20px;display:flex;align-items:center;padding:0 80px;gap:60px}
.why-visual{width:520px;height:340px;background:linear-gradient(160deg,#e7e7e7,#c9c9c9 60%,#a8a8a8)}
.why-copy h2{font-family:"Libre Baskerville",serif;font-weight:400;font-size:34px;color:var(--ink);margin-bottom:30px}
.why-list{list-style:none}
.why-list li{display:flex;gap:14px;font-size:13px;line-height:1.7;color:var(--muted);margin-bottom:18px;width:440px}
.why-list svg{flex:none;margin-top:3px}

/* testimonials */
.testimonials{height:540px;padding-top:50px;text-align:center}
.testimonials h2{font-family:"Libre Baskerville",serif;font-weight:400;font-size:34px;color:var(--ink)}
.testimonials .lead{font-size:13px;color:var(--muted);margin:12px 0 42px}
.quotes{display:flex;gap:60px;padding:0 80px;text-align:left}
.quote{flex:1}
.quote-box{position:relative;border:1px solid var(--rule);padding:34px 34px 34px 60px;font-size:13px;line-height:1.8;color:var(--muted);height:210px}
.quote-box .mark{position:absolute;left:22px;top:22px;font-family:"Lora",serif;font-size:40px;color:var(--accent);line-height:1}
.quote-box::after{content:"";position:absolute;left:50px;bottom:-12px;width:22px;height:22px;background:var(--white);border-right:1px solid var(--rule);border-bottom:1px solid var(--rule);transform:rotate(45deg)}
.quote-name{font-family:"Libre Baskerville",serif;font-size:16px;color:var(--ink);margin:40px 0 6px}
.quote-role{font-size:12px;font-style:italic;color:var(--muted)}

/* footer */
.site-footer{background:var(--navy);height:260px;color:var(--white);position:relative}
.footer-brand{display:flex;justify-content:center;align-items:center;gap:12px;padding-top:26px;font-family:"Libre Baskerville",serif;font-size:22px}
.footer-rule{border:0;border-top:1px solid rgba(255,255,255,.25);margin:24px 80px 0}
.contacts{display:flex;justify-content:space-between;padding:26px 80px 0}
.contact{display:flex;gap:14px;align-items:center;width:300px}
.contact-icon{width:48px;height:48px;border-radius:50%;border:1px solid rgba(255,255,255,.6);display:flex;align-items:center;justify-content:center;flex:none}
.contact h3{font-family:"Libre Baskerville",serif;font-weight:400;font-size:16px}
.contact p{font-size:12px;color:#b9c8d8;margin-top:4px}
.footer-bar{position:absolute;left:0;right:0;bottom:0;height:48px;background:var(--navy-deep);display:flex;align-items:center;padding:0 80px;font-size:11px;color:#a9b8c8}
.social{margin-left:auto;display:flex;gap:10px}
.social span{width:26px;height:26px;border-radius:50%;border:1px solid #a9b8c8}
</style>
</head>
<body>

<header class="hero">
  <div class="hero-visual" role="img" aria-label="Blue digital background with glowing hexagon icons for health, data and emergency services"></div>
  <nav class="site-nav">
    <div class="brand"><span class="brand-square"></span>Pellworth &amp; Quine</div>
    <div class="nav-links"><span>HOME</span><span>ABOUT US</span><span>SERVICES</span><span>CONTACT US</span></div>
    <div class="nav-badge" role="img" aria-label="Certification badge"></div>
  </nav>
  <div class="hero-copy">
    <h1>Pellworth Quine</h1>
    <p>Pellworth &amp; Quine, LLC is a minority owned Service Disabled Veteran Owned Small Business (SDVOSB) that provides Strategic Planning, Public Health Emergency Response, and Data Management Solutions for Federal Civilian and Defense Agencies.</p>
  </div>
  <div class="slider-dots"><span class="active"></span><span></span></div>
</header>

<section class="services">
  <article class="service">
    <div class="service-visual v-disaster" role="img" aria-label="Emergency responders in protective suits"></div>
    <h2>Disaster Response</h2>
    <p>Our teams stand ready to deploy personnel and assets into hot zones, coordinating public health emergency response with speed, discipline and care for every community we serve.</p>
  </article>
  <article class="service">
    <div class="service-visual v-strategy" role="img" aria-label="Planning session with charts on a desk"></div>
    <h2>Strategic Planning</h2>
    <p>We help federal agencies shape concepts of operations, align resources to mission goals and build clear roadmaps that turn complex plans into measurable, lasting results.</p>
  </article>
  <article class="service">
    <div class="service-visual v-data" role="img" aria-label="Laptop showing data management dashboard"></div>
    <h2>Database Management</h2>
    <p>From cloud migration to disaster recovery, we design data replication, consolidation and records management strategies that keep critical information secure and available.</p>
  </article>
</section>

<section class="why">
  <div class="why-visual" role="img" aria-label="Strategic plan sketched on a brick wall"></div>
  <div class="why-copy">
    <h2>Why Hire Us?</h2>
    <ul class="why-list">
      <li><svg width="14" height="14" viewBox="0 0 14 14"><path d="M2 7l3 3 7-7" fill="none" stroke="#2f6ea3" stroke-width="2"/></svg>Over 20 years of experience deploying assets and personnel to disaster zones around the US and the world.</li>
      <li><svg width="14" height="14" viewBox="0 0 14 14"><path d="M2 7l3 3 7-7" fill="none" stroke="#2f6ea3" stroke-width="2"/></svg>Over 20 years of experience developing concept of operations and stakeholder management strategies for Defense Agencies.</li>
      <li><svg width="14" height="14" viewBox="0 0 14 14"><path d="M2 7l3 3 7-7" fill="none" stroke="#2f6ea3" stroke-width="2"/></svg>Over 20 years of experience with database management and migration.</li>
      <li><svg width="14" height="14" viewBox="0 0 14 14"><path d="M2 7l3 3 7-7" fill="none" stroke="#2f6ea3" stroke-width="2"/></svg>Highly educated consultants with over 80% possessing advanced degrees and industry certifications.</li>
    </ul>
  </div>
</section>

<section class="testimonials">
  <h2>Our Testimonials</h2>
  <p class="lead">Hear what federal partners say about working with our team on missions that matter.</p>
  <div class="quotes">
    <div class="quote">
      <div class="quote-box"><span class="mark">&ldquo;</span>Mr. Pellworth served as a trusted advisor throughout our emergency response program. His team planned and deployed critical resources on schedule, and their communication never faltered. Their documentation, discipline and steady leadership gave our agency confidence during a demanding period.</div>
      <p class="quote-name">Col. (Ret.) Marcus T. Delane</p>
      <p class="quote-role">Chief Executive Officer</p>
    </div>
    <div class="quote">
      <div class="quote-box"><span class="mark">&ldquo;</span>Mr. Quine brings over 20 years of hands-on experience to every engagement. His guidance on our database consolidation effort saved months of rework, and his team delivered secure migration plans that our staff could follow with ease. We would gladly partner with them again.</div>
      <p class="quote-name">Mr. Owen R. Castellan</p>
      <p class="quote-role">Business Development Manager</p>
    </div>
  </div>
</section>

<footer class="site-footer">
  <div class="footer-brand"><span class="brand-square"></span>Pellworth &amp; Quine</div>
  <hr class="footer-rule">
  <div class="contacts">
    <div class="contact">
      <span class="contact-icon"><svg width="20" height="22" viewBox="0 0 20 22"><path d="M10 21s7-7.5 7-12.5A7 7 0 0 0 3 8.5C3 13.5 10 21 10 21z" fill="none" stroke="#fff" stroke-width="1.6"/><circle cx="10" cy="8.5" r="2.5" fill="none" stroke="#fff" stroke-width="1.6"/></svg></span>
      <div><h3>Address :</h3><p>418 Linden Crest Ave, Savannah, GA</p></div>
    </div>
    <div class="contact">
      <span class="contact-icon"><svg width="22" height="16" viewBox="0 0 22 16"><rect x="1" y="1" width="20" height="14" fill="none" stroke="#fff" stroke-width="1.6"/><path d="M1 1l10 8 10-8" fill="none" stroke="#fff" stroke-width="1.6"/></svg></span>
      <div><h3>Email</h3><p>info@pellworthquine.com</p></div>
    </div>
    <div class="contact">
      <span class="contact-icon"><svg width="20" height="20" viewBox="0 0 20 20"><path d="M4 1h4l2 5-3 2a11 11 0 0 0 5 5l2-3 5 2v4a2 2 0 0 1-2 2A17 17 0 0 1 2 3a2 2 0 0 1 2-2z" fill="none" stroke="#fff" stroke-width="1.6"/></svg></span>
      <div><h3>Phone</h3><p>Mobile : (555) 201-8847</p></div>
    </div>
  </div>
  <div class="footer-bar">
    <span>&copy; Copyright 2018 Pellworth &amp; Quine All Rights Reserved.</span>
    <div class="social"><span></span><span></span></div>
  </div>
</footer>

</body>
</html>
```